BrimFalcon Business Cards

We have a defined brand. Please visit our website to get a feel for the product and the color pallets. www.brimfalcon-example.com

We need an updated, world class business card design. (See the attached existing card design). Please utilize BOTH sides of the card as shown and be creative with the layout. I do want the horse head icon to be positioned as it is with the existing card.

The remainder of the layout can be customized and I also want it vertically oriented.

Attached are the logo files and please use the colors as follows:
Green - #A5CE39
Tan - #CDBD99
Black

Feel free to play with the colors.

```html
<!DOCTYPE html>
<html lang="en">
<head>
<meta charset="utf-8">
<title>BrimFalcon Business Cards</title>
<link rel="stylesheet" href="https://fonts.googleapis.com/css2?family=Open+Sans:wght@400;600;700&family=Michroma&display=swap">
<style>
  :root {
    --page: #262626;
    --card: #ffffff;
    --ink: #111111;
    --ink-soft: #333333;
    --lime: #b5cc2e;
    --green-deep: #4f9a45;
    --green-light: #b8d233;
    --band: #353535;
    --emblem: #0d0d0d;
  }
  * { box-sizing: border-box; margin: 0; padding: 0; }
  html, body { width: 1200px; height: 1199px; overflow: hidden; }
  body {
    background: var(--page);
    font-family: "Open Sans", sans-serif;
    color: var(--ink);
    position: relative;
  }
  .card {
    position: absolute;
    top: 180px;
    width: 480px;
    height: 840px;
    background: var(--card);
    overflow: hidden;
    box-shadow: 0 10px 30px rgba(0,0,0,.5);
  }
  .card--front { left: 80px; }
  .card--back { left: 640px; }

  .brand { display: flex; flex-direction: column; }
  .brand__name {
    font-weight: 700;
    color: var(--ink);
    letter-spacing: .01em;
    line-height: 1;
  }
  .brand__tagline {
    font-weight: 600;
    color: var(--ink-soft);
    letter-spacing: .32em;
  }
  .card--front .brand {
    position: absolute; left: 0; right: 0; top: 370px; align-items: center;
  }
  .card--front .brand__name { font-size: 64px; }
  .card--front .brand__tagline { font-size: 16px; margin-top: 12px; }

  .card--back .brand { position: absolute; left: 40px; top: 44px; }
  .card--back .brand__name { font-size: 42px; }
  .card--back .brand__tagline { font-size: 12px; margin-top: 7px; }

  .back__shapes { position: absolute; inset: 0; }

  .emblem-slot {
    position: absolute;
    left: 250px; top: 645px;
    width: 160px; height: 160px;
    border-radius: 50%;
    background: radial-gradient(circle at 50% 50%, var(--emblem) 0%, var(--emblem) 55%, rgba(13,13,13,.85) 100%);
  }

  .person { position: absolute; left: 40px; top: 160px; }
  .person__name {
    font-family: "Michroma", sans-serif;
    font-size: 20px;
    letter-spacing: .22em;
    color: var(--lime);
  }
  .person__role { font-size: 14px; color: var(--ink); margin-top: 4px; }

  .contact { position: absolute; left: 40px; top: 240px; list-style: none; }
  .contact__item {
    display: flex; align-items: flex-start; gap: 14px;
    font-size: 15px; color: var(--ink-soft); margin-bottom: 13px;
    line-height: 1.3;
  }
  .contact__icon { flex: 0 0 20px; width: 20px; height: 20px; }
  .contact__icon circle { fill: var(--lime); }
  .contact__icon .glyph { fill: #fff; stroke: none; }
  .contact__icon .stroke { fill: none; stroke: #fff; stroke-width: 1.4; }
</style>
</head>
<body>

<section class="card card--front" aria-label="Card front">
  <div class="brand">
    <span class="brand__name">BrimFalcon</span>
    <span class="brand__tagline">Performance Driven EVs</span>
  </div>
</section>

<section class="card card--back" aria-label="Card back">
  <svg class="back__shapes" width="480" height="840" viewBox="0 0 480 840" aria-hidden="true">
    <defs>
      <radialGradient id="wedgeGlow" cx="90%" cy="20%" r="90%">
        <stop offset="0" stop-color="var(--green-light)"/>
        <stop offset="1" stop-color="var(--green-deep)"/>
      </radialGradient>
      <radialGradient id="panelGlow" cx="55%" cy="60%" r="60%">
        <stop offset="0" stop-color="var(--green-light)"/>
        <stop offset="1" stop-color="var(--green-deep)"/>
      </radialGradient>
    </defs>
    <polygon points="480,400 480,500 330,581" fill="url(#wedgeGlow)"/>
    <polygon points="480,500 480,540 0,800 0,760" fill="var(--band)"/>
    <polygon points="480,540 480,840 0,840 0,800" fill="url(#panelGlow)"/>
  </svg>

  <div class="emblem-slot" role="img" aria-label="Brand emblem placement"></div>

  <div class="brand">
    <span class="brand__name">BrimFalcon</span>
    <span class="brand__tagline">Performance Driven EVs</span>
  </div>

  <div class="person">
    <p class="person__name">DANA MERCER</p>
    <p class="person__role">CEO/Managing Director</p>
  </div>

  <ul class="contact">
    <li class="contact__item">
      <svg class="contact__icon" viewBox="0 0 20 20" aria-label="Phone"><circle cx="10" cy="10" r="10"/><path class="glyph" d="M7 5l2 2-1 1.5c.6 1.4 1.6 2.4 3 3L12.5 10l2 2-1.5 2C9 13.5 6.5 11 6 7z"/></svg>
      <span>555-010-4471</span>
    </li>
    <li class="contact__item">
      <svg class="contact__icon" viewBox="0 0 20 20" aria-label="Office"><circle cx="10" cy="10" r="10"/><path class="glyph" d="M10 4.5l5.5 5h-1.7V15h-2.6v-3.2H8.8V15H6.2V9.5H4.5z"/></svg>
      <span>555-010-4471</span>
    </li>
    <li class="contact__item">
      <svg class="contact__icon" viewBox="0 0 20 20" aria-label="Email"><circle cx="10" cy="10" r="10"/><rect class="stroke" x="5" y="6.5" width="10" height="7"/><path class="stroke" d="M5 6.5l5 4 5-4"/></svg>
      <span>dana.mercer@example.com</span>
    </li>
    <li class="contact__item">
      <svg class="contact__icon" viewBox="0 0 20 20" aria-label="Website"><circle cx="10" cy="10" r="10"/><circle class="stroke" cx="10" cy="10" r="5" style="fill:none"/><path class="stroke" d="M5 10h10M10 5c-2 3-2 7 0 10M10 5c2 3 2 7 0 10"/></svg>
      <span>www.brimfalcon-example.com</span>
    </li>
    <li class="contact__item">
      <svg class="contact__icon" viewBox="0 0 20 20" aria-label="Address"><circle cx="10" cy="10" r="10"/><path class="glyph" d="M10 4a4 4 0 0 1 4 4c0 3-4 8-4 8s-4-5-4-8a4 4 0 0 1 4-4zm0 2.5a1.5 1.5 0 1 0 0 3 1.5 1.5 0 0 0 0-3z"/></svg>
      <span>48 Harbor Lane NW<br>Suite 210, Lakeview MI 00000</span>
    </li>
  </ul>
</section>

</body>
</html>
```